Tidewell Comforts, a portable luxury restroom trailer company needs a landing page

We need a landing page for a luxury portable restroom trailer company. This should be modern, and simple - use any combination of Pantone colors: Warm Gray 1C, Black 7C, 7529c, 873C, 8003C

We rent these trailers for special events like weddings, private parties, festivals, family reunions, team building, wine tastings, beer tastings, food truck round-ups, etc.

An idea of the landing page is in the files below. Please use stock photography and placeholder text for now. The winning design will be given final content.

Requirements
Must have
• Multiple "Get Quote" buttons or a place for them to type in type of rental, how many people etc

```html
<!DOCTYPE html>
<html lang="en">
<head>
<meta charset="utf-8">
<title>Tidewell Comforts — Luxury Portable Restrooms</title>
<link rel="stylesheet" href="https://fonts.googleapis.com/css2?family=Marcellus&family=Noto+Serif:wght@400;700&family=Open+Sans:wght@400;600&display=swap">
<style>
:root{
  --navy:#1e2231;
  --navy-2:#2a3042;
  --gold:#d8c08a;
  --tan:#9c8562;
  --gray:#e3e4e8;
  --white:#ffffff;
  --ink:#1b1f2b;
}
*{margin:0;padding:0;box-sizing:border-box}
html,body{width:1200px;height:3750px;overflow:hidden}
body{position:relative;font-family:'Open Sans',sans-serif;color:var(--ink);background:var(--white)}
.abs{position:absolute}
.serif{font-family:'Noto Serif',serif;font-weight:700}
.logo{font-family:'Marcellus',serif;font-weight:400}

.site-header{position:absolute;left:0;top:0;width:1200px;height:76px;background:var(--white);box-shadow:0 2px 8px rgba(0,0,0,.12);z-index:5}
.site-header .logo{position:absolute;left:110px;top:18px;font-size:30px;color:var(--navy)}
.main-nav a{position:absolute;top:28px;font-size:17px;color:var(--ink);text-decoration:none}
.main-nav .active::after{content:"";position:absolute;left:50%;bottom:-28px;width:44px;margin-left:-22px;height:3px;background:var(--tan)}
.btn{position:absolute;display:flex;align-items:center;justify-content:center;border-radius:30px;font-size:18px;text-decoration:none}
.btn-dark{background:var(--navy);color:var(--white);border:2px solid var(--white);box-shadow:0 0 0 1px var(--navy)}
.btn-outline{color:var(--white);border:2px solid var(--white)}

.hero{position:absolute;left:0;top:76px;width:1200px;height:617px;overflow:hidden;background:var(--navy)}
.photo{position:absolute;border:3px solid var(--white)}
.hero-title{position:absolute;left:476px;top:472px;font-family:'Noto Serif',serif;font-weight:400;font-size:34px;color:var(--gold);white-space:nowrap}

.section-title{position:absolute;left:0;width:1200px;text-align:center;font-size:35px;color:var(--navy)}
.title-rule{position:absolute;left:560px;width:80px;height:4px;border-radius:2px;background:var(--tan)}

.event-card{position:absolute;top:910px;width:299px;height:395px;box-shadow:0 4px 10px rgba(0,0,0,.25)}
.event-card span{position:absolute;left:0;right:0;bottom:52px;text-align:center;color:var(--white);font-family:'Noto Serif',serif;font-weight:700;font-size:22px}
.arrow{position:absolute;top:1088px;width:24px;height:40px}

.products{position:absolute;left:0;top:1414px;width:1200px;height:523px;background:linear-gradient(135deg,#e9eaee,#d9dbe0 55%,#e6e7eb)}
.product-band{position:absolute;left:0;top:1937px;width:1200px;height:388px;background:linear-gradient(135deg,#2d3346,#1e2231 60%,#262b3b)}
.product-ada{position:absolute;left:0;top:2325px;width:1200px;height:446px;background:linear-gradient(135deg,#e6e7eb,#d6d8de 60%,#e4e5e9)}
.product-name{position:absolute;font-size:23px}
.product-text{position:absolute;width:475px;font-size:17.5px;line-height:30px}

.contact{position:absolute;left:0;top:2771px;width:1200px;height:652px;background:linear-gradient(180deg,#8f7a58,#9e8863 40%,#957f5c)}
.field{position:absolute;height:48px;background:var(--white);border:1px solid #cfc6b4;border-radius:2px;font-size:14px;color:#444;padding:15px 17px}

.site-footer{position:absolute;left:0;top:3423px;width:1200px;height:327px;background:var(--navy);color:var(--white)}
.foot-nav a{position:absolute;top:165px;font-size:16px;color:var(--white);text-decoration:none}
.foot-nav i{position:absolute;top:172px;width:7px;height:7px;border-radius:50%;background:var(--white)}
.vrule{position:absolute;top:64px;width:1px;height:124px;background:#4a5063}
.label{position:absolute;font-family:'Noto Serif',serif;font-weight:400;font-size:19px}
.small{position:absolute;font-size:15px;line-height:23px}
.social{position:absolute;top:152px;width:40px;height:40px;border:2px solid var(--white);border-radius:50%;display:flex;align-items:center;justify-content:center}
</style>
</head>
<body>

<header class="site-header">
  <div class="logo">Tidewell Comforts</div>
  <nav class="main-nav">
    <a class="active" href="#" style="left:437px">Home</a>
    <a href="#" style="left:520px">Event</a>
    <a href="#" style="left:600px">Product</a>
    <a href="#" style="left:699px">Contact</a>
  </nav>
  <a class="btn btn-dark" href="#quote" style="left:920px;top:12px;width:168px;height:52px">Get a quote</a>
</header>

<section class="hero">
  <svg class="abs" width="1200" height="617" style="left:0;top:0">
    <polygon points="0,0 1200,0 0,617" fill="#ffffff"/>
    <polygon points="1200,0 1200,617 0,617" fill="#1e2231"/>
    <rect x="676" y="200" width="300" height="417" fill="#2a3042"/>
  </svg>
  <div class="abs" style="left:77px;top:30px;width:243px;height:32px;background:#e3e4ef"></div>
  <div class="photo" role="img" aria-label="White restroom trailer under palm trees" style="left:36px;top:62px;width:328px;height:306px;border:0;background:linear-gradient(180deg,#7a8a6a,#dfe3e6 55%,#9a9a95)"></div>
  <div class="photo" role="img" aria-label="Turquoise portable restroom in a sunny park" style="left:381px;top:22px;width:430px;height:429px;background:linear-gradient(135deg,#3e6b2c,#3fb8cf 45%,#2a86a8 70%,#4f7a33)"></div>
  <div class="photo" role="img" aria-label="White restroom trailer beside a wooden fence" style="left:828px;top:20px;width:334px;height:186px;background:linear-gradient(135deg,#6b4a3a,#eef0f2 45%,#555)"></div>
  <div class="photo" role="img" aria-label="Row of turquoise portable restrooms outdoors" style="left:830px;top:220px;width:138px;height:192px;background:linear-gradient(180deg,#b9c6d8,#40c3c9 50%,#d28a4a)"></div>
  <div class="photo" role="img" aria-label="Blue and white portable restroom" style="left:968px;top:262px;width:194px;height:324px;background:linear-gradient(180deg,#3d5a30,#f3f3f3 35%,#2f6fb0 60%,#e8e8e8)"></div>
  <div class="photo" role="img" aria-label="Accessible restroom trailer with ramp by a red wall" style="left:20px;top:317px;width:198px;height:200px;background:linear-gradient(135deg,#a6262a,#c9ced6 45%,#8a8f96)"></div>
  <div class="photo" role="img" aria-label="Silver restroom trailer on a lawn" style="left:242px;top:397px;width:201px;height:201px;background:linear-gradient(135deg,#2e3a24,#bfc3c8 50%,#3b4a2c)"></div>
  <h1 class="hero-title">Luxury Portable Restroom</h1>
  <a class="btn btn-outline" href="#quote" style="left:473px;top:533px;width:171px;height:54px">Get a quote</a>
</section>

<h2 class="section-title serif" style="top:770px">EVENTS</h2>
<div class="title-rule" style="top:828px"></div>

<svg class="arrow" style="left:38px" viewBox="0 0 24 40"><path d="M20 2 L4 20 L20 38" fill="none" stroke="#7b7f8a" stroke-width="2"/></svg>
<div class="event-card" role="img" aria-label="Wedding table with white flowers" style="left:110px;background:linear-gradient(180deg,#6b6f55,#8d8f86 35%,#2b3040 80%,#1e2231)"><span>Wedding Events</span></div>
<div class="event-card" role="img" aria-label="Hands raising champagne glasses" style="left:451px;background:linear-gradient(180deg,#8a3a2c,#c9876a 35%,#3a2e34 75%,#1e2231)"><span>Private Parties</span></div>
<div class="event-card" role="img" aria-label="Family gathered around an outdoor table" style="left:789px;background:linear-gradient(180deg,#c9b67a,#8a8563 35%,#3a3c46 75%,#1e2231)"><span>Family Reunions</span></div>
<svg class="arrow" style="left:1136px" viewBox="0 0 24 40"><path d="M4 2 L20 20 L4 38" fill="none" stroke="#1e2231" stroke-width="2.5"/></svg>

<section class="products">
  <h2 class="section-title serif" style="top:76px">PRODUCTS</h2>
  <div class="title-rule" style="top:134px"></div>
  <h3 class="product-name serif" style="left:110px;top:234px">2 Station Portable Luxury Restroom</h3>
  <p class="product-text" style="left:110px;top:291px">Lorem ipsum dolor sit amet, consectetur adipiscing elit, sed do eiumod tempor incididunt ut labore et doloregna aliqua. Ut enim ad minim veniam, quis nost exercitation.</p>
  <a class="btn btn-dark" href="#" style="left:110px;top:412px;width:167px;height:52px">Learn more</a>
  <div class="abs" role="img" aria-label="Two grey portable restroom stations side by side" style="left:779px;top:177px;width:298px;height:297px;background:linear-gradient(90deg,#6e7a90,#8591a6 50%,#6e7a90);border-radius:10px 10px 2px 2px"></div>
</section>

<section class="product-band">
  <div class="abs" role="img" aria-label="White three station restroom trailer" style="left:109px;top:68px;width:405px;height:249px;background:linear-gradient(180deg,#e9ecf0,#c9ced6 70%,#2a2a2a);border-radius:4px"></div>
  <h3 class="product-name serif" style="left:619px;top:77px;color:var(--white)">3 Station Portable Luxury Restroom</h3>
  <p class="product-text" style="left:619px;top:134px;color:var(--white)">Lorem ipsum dolor sit amet, consectetur adipiscing elit, sed do eiumod tempor incididunt ut labore et doloregna aliqua. Ut enim ad minim veniam, quis nost exercitation.</p>
  <a class="btn btn-outline" href="#" style="left:617px;top:254px;width:169px;height:54px">Learn more</a>
</section>

<section class="product-ada">
  <h3 class="product-name serif" style="left:110px;top:63px">ADA Restroom</h3>
  <p class="product-text" style="left:110px;top:119px">Lorem ipsum dolor sit amet, consectetur adipiscing elit, sed do eiumod tempor incididunt ut labore et dolorem aliqua. Ut enim ad minim veniam, quis nos exercitation.</p>
  <a class="btn btn-dark" href="#" style="left:110px;top:240px;width:167px;height:52px">Learn more</a>
  <div class="abs" role="img" aria-label="White accessible restroom trailer with ramp" style="left:709px;top:22px;width:383px;height:318px;background:linear-gradient(160deg,#f4f5f7,#d3d6dc 60%,#9aa0a8)"></div>
  <svg class="abs" style="left:584px;top:400px" width="34" height="20" viewBox="0 0 34 20"><path d="M2 3 L17 17 L32 3" fill="none" stroke="#1e2231" stroke-width="3"/></svg>
</section>

<section class="contact" id="quote">
  <h2 class="section-title serif" style="top:76px;color:var(--white);font-size:36px">CONTACT US FOR A QUOTE</h2>
  <div class="title-rule" style="top:134px;background:var(--white)"></div>
  <form>
    <div class="field" style="left:262px;top:202px;width:334px">Name :</div>
    <div class="field" style="left:605px;top:202px;width:334px">Email :</div>
    <div class="field" style="left:262px;top:263px;width:334px">Phone :</div>
    <div class="field" style="left:605px;top:263px;width:334px">Type of Event :</div>
    <div class="field" style="left:262px;top:324px;width:677px">Type of product you're interested in :</div>
    <div class="field" style="left:262px;top:384px;width:334px">When do you need :</div>
    <div class="field" style="left:605px;top:384px;width:334px">For how long :</div>
    <div class="field" style="left:262px;top:444px;width:677px">Address :</div>
    <a class="btn btn-dark" href="#" style="left:514px;top:518px;width:170px;height:56px">Submit</a>
  </form>
</section>

<footer class="site-footer">
  <div class="logo abs" style="left:110px;top:80px;font-size:38px">Tidewell Comforts</div>
  <nav class="foot-nav">
    <i style="left:111px"></i><a href="#" style="left:134px">Event</a>
    <i style="left:194px"></i><a href="#" style="left:222px">Product</a>
    <i style="left:300px"></i><a href="#" style="left:329px">Contact</a>
  </nav>
  <div class="vrule" style="left:447px"></div>
  <div class="vrule" style="left:776px"></div>

  <svg class="abs" style="left:492px;top:76px" width="18" height="24" viewBox="0 0 18 24"><path d="M9 22 C4 15 2 11 2 8 A7 7 0 0 1 16 8 C16 11 14 15 9 22 Z" fill="none" stroke="#fff" stroke-width="1.5"/><circle cx="9" cy="8" r="2.5" fill="none" stroke="#fff" stroke-width="1.5"/></svg>
  <div class="label" style="left:530px;top:66px">ADDRESS</div>
  <div class="small" style="left:531px;top:90px">Tidewell Comforts, 41<br>Harbor Lane</div>
  <a class="social" href="#" aria-label="Share link" style="left:532px">
    <svg width="20" height="20" viewBox="0 0 20 20"><path d="M8.5 11.5 L11.5 8.5 M7 9 L5 11 A3 3 0 0 0 9 15 L11 13 M13 11 L15 9 A3 3 0 0 0 11 5 L9 7" fill="none" stroke="#fff" stroke-width="1.8" stroke-linecap="round"/></svg>
  </a>
  <a class="social" href="#" aria-label="Message us" style="left:584px">
    <svg width="20" height="20" viewBox="0 0 20 20"><path d="M3 4 H17 V13 H8 L4 16 V13 H3 Z" fill="none" stroke="#fff" stroke-width="1.7" stroke-linejoin="round"/></svg>
  </a>

  <svg class="abs" style="left:829px;top:78px" width="22" height="22" viewBox="0 0 22 22"><path d="M4 2 L8 2 L10 7 L7.5 9 C9 12.5 10.5 14 14 15.5 L16 13 L21 15 L21 19 C21 20 20 21 19 21 C9 20 2 13 1 4 C1 3 2 2 4 2 Z" fill="none" stroke="#fff" stroke-width="1.4"/></svg>
  <div class="label" style="left:869px;top:66px">PHONE</div>
  <div class="small" style="left:869px;top:90px">+1 555-014-2290</div>

  <svg class="abs" style="left:831px;top:146px" width="22" height="16" viewBox="0 0 22 16"><rect x="1" y="1" width="20" height="14" fill="none" stroke="#fff" stroke-width="1.4"/><path d="M1 1 L11 9 L21 1 M1 15 L8 7 M21 15 L14 7" fill="none" stroke="#fff" stroke-width="1.4"/></svg>
  <div class="label" style="left:871px;top:135px">EMAIL</div>
  <div class="small" style="left:871px;top:159px">hello@tidewellcomforts.example</div>

  <div class="abs" style="left:0;top:246px;width:1200px;height:1px;background:#3a4054"></div>
  <div class="abs" style="left:0;top:276px;width:1200px;text-align:center;font-size:17px">Tidewell Comforts © 2022.All Rights Reserved.</div>
</footer>

</body>
</html>
```